Velmora Consulting Business

** Please add the content information from my old business card
1. I would like to see a two sided business card with both options with the 1st Option--Tallow Spire-new WHITE BACKGROUND LOGO
2 nd Option-Tallow Spire - new BLACK- Background Logo
3rd -Option a business card with my Photo on the card
Please add the new word to the card information:
EXECUTION
AS THE OWNER'S REP
WE AIM TO ACHIEVE YOUR
INFRASTRUCTURE VISION with
OUR SPECIALIZATION & EXECUTION in:

FUNDING Planning
BUSINESS Planning
INFRASTRUCTURE Planning
PROJECT Management
Since 2012
_____________________________________________________________________
I want to get spot uv raised printing. I was liking a a nice rich white linen paper stock with black writing & NOT A COLORED CARD other than a variety of white or black cards concept

```html
<!DOCTYPE html>
<html lang="en">
<head>
<meta charset="utf-8">
<title>Velmora Consulting – Business Card Concepts</title>
<link href="https://fonts.googleapis.com/css2?family=Montserrat:wght@400;500;600;700&display=swap" rel="stylesheet">
<style>
  :root {
    --stage: #a9adab;
    --paper: #ffffff;
    --ink: #1a1a1a;
    --card-dark: #161616;
    --accent: #e3173a;
    --text-light: #f2f2f2;
    --text-dark: #222222;
  }
  * { box-sizing: border-box; margin: 0; padding: 0; }
  html, body { width: 1200px; height: 1118px; overflow: hidden; }
  body {
    background: var(--stage);
    font-family: "Montserrat", sans-serif;
    position: relative;
  }
  .card {
    position: absolute;
    border-radius: 16px;
    overflow: hidden;
    background: var(--card-dark);
    color: var(--text-light);
  }
  .card--white { background: var(--paper); color: var(--text-dark); }

  /* positions */
  .card--front-white { left: 14px; top: 15px; width: 573px; height: 342px; }
  .card--back-a { left: 608px; top: 15px; width: 570px; height: 349px; }
  .card--front-black { left: 17px; top: 389px; width: 576px; height: 344px; }
  .card--back-b { left: 616px; top: 392px; width: 566px; height: 340px; }
  .card--front-photo { left: 26px; top: 757px; width: 573px; height: 343px; }
  .card--back-c { left: 625px; top: 760px; width: 557px; height: 332px; }

  /* brand name block */
  .brand { position: absolute; font-weight: 600; line-height: 1; }
  .brand__name { display: block; font-size: 40px; letter-spacing: -0.5px; }
  .brand__sub { display: block; font-size: 12px; letter-spacing: 9.2px; margin-top: 8px; }
  .brand--ink { color: var(--ink); }
  .brand--light { color: #ffffff; }

  /* person */
  .person__name { color: var(--accent); font-weight: 700; font-size: 21.5px; white-space: nowrap; }
  .person__title { font-size: 13px; font-weight: 400; letter-spacing: 0.1px; margin-top: 3px; white-space: nowrap; }
  .person__city { font-size: 13px; white-space: nowrap; }

  .contact { list-style: none; font-size: 13px; }
  .contact li { display: flex; align-items: center; gap: 11px; height: 19px; }
  .contact svg { width: 13px; height: 13px; flex: none; fill: var(--accent); }

  /* front white */
  .card--front-white .brand { left: 68px; top: 178px; }
  .card--front-white .rule { position: absolute; left: 246px; top: 105px; width: 2px; height: 136px; background: var(--accent); }
  .card--front-white .person { position: absolute; left: 253px; top: 103px; }
  .card--front-white .person__city { margin-top: 13px; }
  .card--front-white .contact { margin-top: 10px; }
  .band { position: absolute; left: 0; bottom: 0; width: 100%; height: 9px; }

  /* front black */
  .card--front-black .brand { left: 27px; top: 40px; }
  .card--front-black .person { position: absolute; right: 34px; top: 45px; text-align: right; }
  .card--front-black .tab { position: absolute; right: 0; top: 45px; width: 14px; height: 39px; background: var(--accent); }
  .card--front-black .details { position: absolute; left: 27px; top: 222px; }
  .card--front-black .contact { margin-top: 18px; }

  /* front photo */
  .portrait {
    position: absolute; left: 0; top: 0; width: 238px; height: 100%;
    background: radial-gradient(ellipse at 45% 40%, #6e4a3a 0%, #3a2a24 35%, #121212 75%);
  }
  .card--front-photo { background: #0e0e10; }
  .card--front-photo .brand { left: 268px; top: 88px; }
  .card--front-photo .person { position: absolute; left: 269px; top: 182px; }
  .card--front-photo .person__city { margin-top: 14px; }
  .card--front-photo .contact { margin-top: 6px; }

  /* back */
  .back .brand { left: 26px; top: 50px; }
  .tagline {
    position: absolute; left: 27px; top: 138px;
    color: var(--accent); font-weight: 700; font-size: 12px; line-height: 16.5px; text-transform: uppercase;
  }
  .tagline .lower { text-transform: none; }
  .services { position: absolute; left: 24px; top: 225px; list-style: none; font-size: 13px; }
  .services li { display: flex; align-items: center; gap: 8px; height: 22px; }
  .services li::before { content: ""; width: 8px; height: 8px; background: var(--accent); }
  .since {
    position: absolute; left: 164px; top: 311px; font-size: 13px;
    padding-bottom: 3px; border-bottom: 2px solid var(--accent);
  }
  .back-glow {
    position: absolute; right: 0; top: 0; width: 45%; height: 100%;
    background: linear-gradient(160deg, rgba(255,255,255,0) 20%, rgba(255,255,255,0.05) 55%, rgba(0,0,0,0.25) 100%);
  }
</style>
</head>
<body>

<svg width="0" height="0" style="position:absolute">
  <symbol id="icon-phone" viewBox="0 0 24 24"><path d="M6.6 10.8a15.1 15.1 0 0 0 6.6 6.6l2.2-2.2a1 1 0 0 1 1-.25 11.4 11.4 0 0 0 3.6.57 1 1 0 0 1 1 1V20a1 1 0 0 1-1 1A17 17 0 0 1 3 4a1 1 0 0 1 1-1h3.5a1 1 0 0 1 1 1c0 1.25.2 2.45.57 3.6a1 1 0 0 1-.25 1z"/></symbol>
  <symbol id="icon-mail" viewBox="0 0 24 24"><path d="M2 5h20v14H2z M2 5l10 7 10-7" /><path d="M2 5h20l-10 7z" fill="#fff" opacity=".35"/></symbol>
  <symbol id="icon-globe" viewBox="0 0 24 24"><circle cx="12" cy="12" r="10"/><path d="M7 7c2 1 3 3 2 5s1 3 0 5M15 4c-1 2 1 3 3 3M14 14c2 0 3 2 2 5" stroke="#fff" stroke-width="1.4" fill="none" opacity=".6"/></symbol>
</svg>

<!-- Option 1: white front -->
<section class="card card--white card--front-white">
  <div class="brand brand--ink"><span class="brand__name">Velmora</span><span class="brand__sub">CONSULTING</span></div>
  <div class="rule"></div>
  <div class="person">
    <p class="person__name">Marguerite Ellison-Varma</p>
    <p class="person__title">CEO / LEAD PROJECT MANAGER</p>
    <p class="person__city">Northgate NT · Riverbend NB</p>
    <ul class="contact">
      <li><svg><use href="#icon-phone"/></svg>555.204.7318</li>
      <li><svg><use href="#icon-mail"/></svg>mara@velmora.ca</li>
      <li><svg><use href="#icon-globe"/></svg>ww.velmora.ca</li>
    </ul>
  </div>
  <svg class="band" viewBox="0 0 573 9" preserveAspectRatio="none">
    <polygon points="0,0 244,0 236,9 0,9" fill="var(--ink)"/>
    <polygon points="250,0 573,0 573,9 242,9" fill="var(--accent)"/>
  </svg>
</section>

<!-- Back A -->
<section class="card back card--back-a">
  <div class="back-glow"></div>
  <div class="brand brand--light"><span class="brand__name">Velmora</span><span class="brand__sub">CONSULTING</span></div>
  <p class="tagline">AS THE OWNER'S REP<br>WE AIM TO ACHIEVE YOUR<br>INFRASTRUCTURE VISION <span class="lower">with</span><br>OUR SPECIALIZATION <span class="lower">in:</span></p>
  <ul class="services">
    <li>FUNDING Planning</li><li>BUSINESS Planning</li><li>INFRASTRUCTURE Planning</li><li>PROJECT Management</li>
  </ul>
  <p class="since">Since 2012</p>
</section>

<!-- Option 2: black front -->
<section class="card card--front-black">
  <div class="back-glow"></div>
  <div class="brand brand--light"><span class="brand__name">Velmora</span><span class="brand__sub">CONSULTING</span></div>
  <div class="person">
    <p class="person__name">Marguerite Ellison-Varma</p>
    <p class="person__title">CEO / LEAD PROJECT MANAGER</p>
  </div>
  <div class="tab"></div>
  <div class="details">
    <p class="person__city">Northgate NT · Riverbend NB</p>
    <ul class="contact">
      <li><svg><use href="#icon-phone"/></svg>555.204.7318</li>
      <li><svg><use href="#icon-mail"/></svg>mara@velmora.ca</li>
      <li><svg><use href="#icon-globe"/></svg>ww.velmora.ca</li>
    </ul>
  </div>
</section>

<!-- Back B -->
<section class="card back card--back-b">
  <div class="back-glow"></div>
  <div class="brand brand--light"><span class="brand__name">Velmora</span><span class="brand__sub">CONSULTING</span></div>
  <p class="tagline">AS THE OWNER'S REP<br>WE AIM TO ACHIEVE YOUR<br>INFRASTRUCTURE VISION <span class="lower">with</span><br>OUR SPECIALIZATION <span class="lower">in:</span></p>
  <ul class="services">
    <li>FUNDING Planning</li><li>BUSINESS Planning</li><li>INFRASTRUCTURE Planning</li><li>PROJECT Management</li>
  </ul>
  <p class="since">Since 2012</p>
</section>

<!-- Option 3: photo front -->
<section class="card card--front-photo">
  <div class="portrait" role="img" aria-label="Portrait photo of the CEO, arms crossed, on a dark backdrop"></div>
  <div class="brand brand--light"><span class="brand__name">Velmora</span><span class="brand__sub">CONSULTING</span></div>
  <div class="person">
    <p class="person__name">Marguerite Ellison-Varma</p>
    <p class="person__title">CEO / LEAD PROJECT MANAGER</p>
    <p class="person__city">Northgate NT · Riverbend NB</p>
    <ul class="contact">
      <li><svg><use href="#icon-phone"/></svg>555.204.7318</li>
      <li><svg><use href="#icon-mail"/></svg>mara@velmora.ca</li>
      <li><svg><use href="#icon-globe"/></svg>ww.velmora.ca</li>
    </ul>
  </div>
</section>

<!-- Back C -->
<section class="card back card--back-c">
  <div class="back-glow"></div>
  <div class="brand brand--light"><span class="brand__name">Velmora</span><span class="brand__sub">CONSULTING</span></div>
  <p class="tagline">AS THE OWNER'S REP<br>WE AIM TO ACHIEVE YOUR<br>INFRASTRUCTURE VISION <span class="lower">with</span><br>OUR SPECIALIZATION <span class="lower">in:</span></p>
  <ul class="services">
    <li>FUNDING Planning</li><li>BUSINESS Planning</li><li>INFRASTRUCTURE Planning</li><li>PROJECT Management</li>
  </ul>
  <p class="since">Since 2012</p>
</section>

</body>
</html>
```